Tovimar Community Development Planning New web site

Design a new web site. I have a budget of $1,500.00.
Attached on PowerPoint is a complete site plan. Home page and linked pages.
10 - 12 pages. All copy and photos will be supplied. (300dpi)
I have shown them the concept which they like.
No data bases required. Home page with animations dissolving.
They former web site has been taken down. They have been in business 30 years in New Jersey
Colors teal blues and greens
There will be a new logo)being designed)
The text in home page copy will give you a detailed story what they are all about.

files have been approved for Tovimar, Inc.   Brenton is the designer

```html
<!DOCTYPE html>
<html lang="en">
<head>
<meta charset="utf-8">
<title>Tovimar — Community Development Planning</title>
<link rel="stylesheet" href="https://fonts.googleapis.com/css2?family=Comfortaa:wght@400&family=Noto+Sans:wght@400;700&family=Arimo:wght@400;700&display=swap">
<style>
:root{
  --ink:#111;
  --dark:#333333;
  --darkest:#2b2b2b;
  --teal:#0ba4b0;
  --green:#a3c46e;
  --lime:#c8dc6a;
  --gold:#fdc300;
  --white:#fff;
}
*{margin:0;padding:0;box-sizing:border-box}
html,body{width:1024px;height:1200px;overflow:hidden;background:var(--white)}
body{position:relative;font-family:"Arimo",Arial,sans-serif;color:var(--ink)}
.abs{position:absolute}
.top-strip{left:0;top:0;width:1024px;height:9px;background:var(--darkest)}
.masthead{left:0;top:9px;width:1024px;height:117px;background:var(--teal)}
.brand{left:16px;top:70px;font-family:"Comfortaa",sans-serif;font-size:35px;color:var(--white);letter-spacing:-0.5px}
.contact{right:12px;top:19px;display:flex;align-items:center;gap:7px;color:var(--white);font-weight:700;font-size:12px;line-height:13px}
.hero{left:0;top:126px;width:1024px;height:346px;background:var(--dark)}
.nav{right:14px;top:133px;display:flex;gap:12px;font-size:17px;color:var(--white)}
.nav li{list-style:none;display:flex;align-items:center;gap:5px}
.nav li::before{content:"";width:4px;height:4px;border-radius:50%;background:var(--lime);margin-top:6px}
.nav .current{color:var(--lime)}
.slider{left:19px;top:171px;width:499px;height:276px;background:var(--green);padding:6px 12px 7px 13px}
.slide-photo{width:100%;height:100%;background:linear-gradient(120deg,#e9ecef 0%,#f7f8fa 45%,#d9dde3 70%,#2f3136 88%)}
.slide-next{left:445px;top:290px}
.slide-dots{left:416px;top:454px;display:flex;gap:3px}
.slide-dots span{width:5px;height:5px;border-radius:50%;background:#777}
.slide-dots span:first-child{background:var(--white)}
.teaser{left:537px;width:466px;border:1px solid var(--gold);padding:14px 12px 0 36px;font-weight:700;font-size:12px;line-height:14px;color:var(--white)}
.teaser::before{content:"";position:absolute;left:6px;top:6px;width:4px;height:4px;background:var(--gold)}
.teaser.featured{background:var(--gold);color:var(--ink)}
.teaser.featured::before{background:var(--ink)}
.tagline{left:140px;top:482px;width:744px;text-align:center;font-size:13.6px;line-height:16.4px}
.section-bar{left:26px;width:972px;height:17px;background:var(--green);color:var(--white);font-size:11.5px;line-height:17px;padding-left:12px}
.intro{left:25px;top:614px;width:975px;font-family:"Noto Sans",Verdana,sans-serif;font-size:12.6px;line-height:14.5px;letter-spacing:0.2px}
.intro p{margin-bottom:14px}
.read-more{left:880px;top:727px;width:58px;height:21px;background:var(--green);color:var(--white);font-size:8.5px;line-height:21px;text-align:center;font-family:"Noto Sans",sans-serif}
.results{left:60px;top:807px;width:945px;font-size:12px;line-height:14.5px;list-style:none}
.results li{position:relative;padding-left:12px;margin-bottom:14.5px}
.results li::before{content:"";position:absolute;left:0;top:6px;width:5px;height:5px;background:var(--green)}
.results .link{text-decoration:underline}
.memberships-title{left:340px;top:1001px;width:344px;height:30px;background:var(--green);color:var(--white);font-size:17.5px;line-height:30px;text-align:center}
.memberships{left:100px;top:1045px;width:824px;text-align:center;font-size:16px;line-height:20px}
.footer{left:0;top:1166px;width:1024px;text-align:center;font-size:12px}
</style>
</head>
<body>
<div class="abs top-strip"></div>
<header class="abs masthead"></header>
<div class="abs brand">Tovimar</div>
<div class="abs contact">
  <svg width="23" height="23" viewBox="0 0 24 24" aria-hidden="true"><circle cx="12" cy="12" r="10.5" fill="none" stroke="#fff" stroke-width="1.8"/><path d="M8.5 6.5l2 2.8-1.3 1.4c.8 1.7 2 2.9 3.7 3.7l1.4-1.3 2.8 2-1.1 1.8c-4.3-.3-8.6-4.6-8.9-8.9z" fill="#fff"/></svg>
  <div>Tel (555) 014-2270<br>Fax (555) 014-2291</div>
</div>

<section class="abs hero"></section>
<ul class="abs nav">
  <li class="current">Home</li>
  <li>Our Company</li>
  <li>Services</li>
  <li>Housing Rehab Application</li>
  <li>Affordable Application</li>
  <li>Contact Us</li>
</ul>

<div class="abs slider">
  <div class="slide-photo" role="img" aria-label="Photo of two hands pointing at architectural building plans"></div>
</div>
<svg class="abs slide-next" width="54" height="54" viewBox="0 0 54 54" aria-hidden="true"><circle cx="27" cy="27" r="27" fill="#555" fill-opacity=".85"/><path d="M22 16l12 11-12 11" fill="none" stroke="#222" stroke-width="6"/></svg>
<div class="abs slide-dots"><span></span><span></span><span></span><span></span></div>

<div class="abs teaser featured" style="top:171px;height:83px">Lorem ipsum dolor sit amet, consectetuer adipiscing elit, sed diam nonummy nibh euismod tincidunt ut laoreet dolore magna aliquam erat volutpat. Ut wisi enim ad minim veniam, quis nostrud exerci tation accumsan et i</div>
<div class="abs teaser" style="top:268px;height:83px">Lorem ipsum dolor sit amet, consectetuer adipiscing elit, sed diam nonummy nibh euismod tincidunt ut laoreet dolore magna aliquam erat volutpat. Ut wisi enim ad minim veniam, quis nostrud exerci tation accumsan et i</div>
<div class="abs teaser" style="top:365px;height:84px">Lorem ipsum dolor sit amet, consectetuer adipiscing elit, sed diam nonummy nibh euismod tincidunt ut laoreet dolore magna aliquam erat volutpat. Ut wisi enim ad minim veniam, quis nostrud exerci tation accumsan et i</div>

<p class="abs tagline">Community Development Planning * Housing Rehabilitation Administration * US Department of Housing and Urban Development (HUD) Program Management * Implementation of Programs under the Jurisdiction of New Jersey Council of Affordable Housing (COAH)</p>

<div class="abs section-bar" style="top:569px">Welcome</div>
<div class="abs intro">
  <p><b>Tovimar, Inc.</b> is a city planning firm that specializes in community development and housing rehabilitation program planning, design and implementation. We have over twenty years of experience in developing and administering income base-base housing and programs in accordance with US Department of Housing and Urban Development (HUD) and New Jersey Council on Affordable Housing (COAH) rules and regulations,</p>
  <p>In addition, our firm is capable of providing the technical and administrative assistance our clients require for implementation of their income based housing programs. Calder Whitfield Associates is one of the most experience urban planning firms in New Jersey, with over forty years of as consulting planners.</p>
  <p>To find out more about federal housing programs that we will administer, please go to<br>www.housingprograms.example</p>
</div>
<div class="abs read-more">Read more</div>

<div class="abs section-bar" style="top:769px;left:28px;width:970px">We get results</div>
<ul class="abs results">
  <li>Tovimar designs income based programs to be supported by federal placement lotteries state funding.</li>
  <li>We implement local programs to benefit people seeking access to affordable housing.</li>
  <li>Our experienced staff screen applicants for local affordable housing.</li>
  <li>We pre-qualify persons who have applied for housing rehabilitation.</li>
  <li><span class="link">Conduct placement lotteries</span></li>
  <li>Through local housing rehabilitation programs, our experience construction inspectors determine what improvements are required at eligible units based on local building codes and health and safety issues.</li>
</ul>

<div class="abs memberships-title">Memberships</div>
<p class="abs memberships">National Neighborhood Renewal Council &nbsp;&nbsp; Garden State Planning Society<br>Coastal Planning Officials Guild &nbsp;Tri-County Housing Development Forum</p>

<footer class="abs footer">Copy Right 2014 Tovimar, 118 Harbor Lane, Brookfield, New Jersey, 08000 &nbsp;&nbsp;TEL (555) 014-2270 Fax (555) 014-2291</footer>
</body>
</html>
```